Woman owned consulting company needs an elegant and modern business card design

I need a business card design for my new consulting company, Mara Quillon Consulting. I am looking for something that is simple and elegant, but also creative and original. You can use either version of the logo that are attached. I have also included the information that needs to be featured on the business card.

Contact Information for Business Card

Requirements
Must have
• The logo and the font type and a standard business card size. Use shades of gray/silver and or rose gold that are in the logo.
• I didn't realize that my actual logo wasn't attached. Please incorporate in the designs.
Should not have
• Colors that are different from my logo

```html
<!DOCTYPE html>
<html lang="en">
<head>
<meta charset="utf-8">
<title>Mara Quillon Consulting – Business Card</title>
<link rel="stylesheet" href="https://fonts.googleapis.com/css2?family=Cinzel:wght@400;600&family=Lora:wght@400&display=swap">
<style>
  :root {
    --backdrop: #c9c9c9;
    --card-dark: #3a3e41;
    --card-light: #f6f6f6;
    --silver: #c4c6c8;
    --silver-mid: #9a9c9e;
    --swoosh: #b5b7b9;
    --ink: #2b2b2b;
    --black: #0d0d0d;
    --white: #ffffff;
  }
  * { box-sizing: border-box; margin: 0; padding: 0; }
  html, body { width: 1200px; height: 852px; overflow: hidden; }
  body {
    background: var(--backdrop);
    position: relative;
    font-family: "Lora", Georgia, serif;
  }
  .card {
    position: absolute;
    width: 490px;
    height: 280px;
    border-radius: 14px;
    overflow: hidden;
    box-shadow: 0 6px 18px rgba(0,0,0,0.18);
  }
  .card--back { left: 70px; top: 286px; background: var(--card-dark); }
  .card--front { left: 640px; top: 286px; background: var(--card-light); }

  .brand {
    position: absolute;
    display: flex;
    align-items: center;
    gap: 14px;
    font-family: "Cinzel", "Times New Roman", serif;
    font-weight: 400;
    line-height: 1.05;
    text-transform: uppercase;
  }
  .brand__dot { width: 14px; height: 14px; border-radius: 50%; flex: none; }
  .brand__name { font-size: 27px; letter-spacing: 1px; }
  .brand__name span { display: block; font-size: 21px; letter-spacing: 1.5px; }

  .card--back .brand { left: 72px; top: 104px; color: var(--silver); }
  .card--back .brand__dot { background: var(--silver); }

  .card--front .brand { left: 40px; top: 36px; color: var(--silver-mid); }
  .card--front .brand__dot { background: var(--silver-mid); }

  .wave { position: absolute; inset: 0; width: 100%; height: 100%; }
  .wave__outer { fill: var(--swoosh); }
  .wave__gap { fill: var(--card-light); }
  .wave__fill { fill: var(--black); }

  .contact {
    position: absolute;
    left: 40px;
    top: 150px;
    list-style: none;
    font-size: 12px;
    color: var(--ink);
  }
  .contact li { display: flex; align-items: center; gap: 10px; height: 19px; }
  .contact svg { width: 11px; height: 11px; fill: var(--ink); flex: none; }

  .holder {
    position: absolute;
    right: 30px;
    top: 160px;
    text-align: right;
    color: var(--white);
    white-space: nowrap;
  }
  .holder__name { font-family: "Cinzel", "Times New Roman", serif; font-weight: 600; font-size: 14px; letter-spacing: 1px; }
  .holder__role { font-size: 10px; margin-top: 3px; }
</style>
</head>
<body>

<section class="card card--back" aria-label="Card back">
  <div class="brand">
    <i class="brand__dot"></i>
    <div class="brand__name">Mara Quillon<span>Consulting, LLC</span></div>
  </div>
</section>

<section class="card card--front" aria-label="Card front">
  <svg class="wave" viewBox="0 0 490 280" preserveAspectRatio="none" aria-hidden="true">
    <path class="wave__outer" d="M490,60 C380,60 310,100 288,165 C266,230 210,266 100,280 L490,280 Z"/>
    <path class="wave__gap" d="M490,72 C390,72 322,110 300,170 C278,232 228,268 140,280 L490,280 Z"/>
    <path class="wave__fill" d="M490,84 C400,84 336,120 314,176 C292,236 246,270 186,280 L490,280 Z"/>
  </svg>

  <div class="brand">
    <i class="brand__dot"></i>
    <div class="brand__name">Mara Quillon<span>Consulting, LLC</span></div>
  </div>

  <ul class="contact">
    <li>
      <svg viewBox="0 0 24 24"><path d="M6.6 10.8a15.1 15.1 0 0 0 6.6 6.6l2.2-2.2a1 1 0 0 1 1-.25 11.4 11.4 0 0 0 3.6.57 1 1 0 0 1 1 1V20a1 1 0 0 1-1 1A17 17 0 0 1 3 4a1 1 0 0 1 1-1h3.5a1 1 0 0 1 1 1c0 1.25.2 2.46.57 3.6a1 1 0 0 1-.25 1z"/></svg>
      610-555-0142
    </li>
    <li>
      <svg viewBox="0 0 24 24"><path d="M2 5h20v14H2z M3.5 6.5 12 13l8.5-6.5" fill="none" stroke="#2b2b2b" stroke-width="2"/></svg>
      mara@maraquillonconsulting.com
    </li>
    <li>
      <svg viewBox="0 0 24 24"><circle cx="12" cy="12" r="10" fill="none" stroke="#2b2b2b" stroke-width="2"/><path d="M2 12h20M12 2c3 3 3 17 0 20M12 2c-3 3-3 17 0 20" fill="none" stroke="#2b2b2b" stroke-width="1.6"/></svg>
      www.maraquillonconsulting.com
    </li>
  </ul>

  <div class="holder">
    <p class="holder__name">MARA QUILLON</p>
    <p class="holder__role">Owner</p>
  </div>
</section>

</body>
</html>
```